Adult dating site banners and payment page concepts

We need an overhaul done on our banners, as well as rebranding our packages. We have uploaded a full description of what we need doing, we are not looking for you do do all of them right now. We are looking for a concept for one site banner, one version of the payment page, and one affiliate banner. We will then pay the winner to do the rest of the design work we need to get them all done, but we have uploaded all the bits we will eventually need.

Colors

Designer to choose colors to be used in the design.

Requirements
Must have
• Banner design brief
• We are looking for a new design for all of our upgrade banners for our adult dating swingers sites as well as our payment pages so they need to appeal to men, women, and couples. We are looking for something fun and sexy that really looks nice on mobile and desktop.
• Important design notes banners
• 1. Where you see the word “Extras” we are changing it to a package called “Plus, this can be the word Plus or the + symbol, or both”, we are looking for a design for this.
• 2. Where you see the word “Premium” we are now calling it “Supporter” so that needs some nice font or design as well.
• 3. We would like the offers to jump out at you with the discounts etc.
• 4. The banners need to be able to work on our different sites on the following colours:
• South Africa #7e0202
• UK #0d72ba
• Canada #147eab
• Ireland #003a15
• Australia #272f47
• New Zealand #446160
• Payment pages
• 1. We would like to keep them clean as most of our users are on mobile
• 2. But if you think they can be improved to help with conversion rates we would like to see it.
• Affiliate banners
• We also advertise our sites on other websites using geo-targeted banners; we need to tempt people to click through. The ones we have right now are not animated and we like the idea of that, something saucy and sexy but not porn related. We would like these to be re designed to be something sexier that grabs your attention.

```html
<!DOCTYPE html>
<html lang="en">
<head>
<meta charset="utf-8">
<title>10th Anniversary Offer Banners</title>
<link rel="stylesheet" href="https://fonts.googleapis.com/css2?family=Open+Sans:wght@300;400;700&display=swap">
<style>
  :root {
    --page-bg: #e4e5e7;
    --frame: #ffffff;
    --sky-top: #2a9ccb;
    --sky-bottom: #4cc3ea;
    --accent: #f7931e;
    --text-light: #ffffff;
    --band: rgba(20, 60, 90, 0.38);
    --skin-light: #e9c2a6;
    --skin-mid: #c99578;
    --mono-dark: #2b2b2b;
    --mono-mid: #6f6f6f;
    --mono-light: #c9c9c9;
  }
  * { box-sizing: border-box; margin: 0; padding: 0; }
  html, body { width: 1200px; height: 1200px; overflow: hidden; }
  body {
    background: var(--page-bg);
    font-family: "Open Sans", Arial, sans-serif;
    position: relative;
  }
  .banner {
    position: absolute;
    left: 46px;
    width: 1108px;
    height: 480px;
    background: var(--frame);
    padding: 14px;
  }
  .banner--sky { top: 54px; }
  .banner--mono { top: 620px; height: 478px; }
  .banner__inner {
    position: relative;
    width: 100%;
    height: 100%;
    overflow: hidden;
  }
  .banner--sky .banner__inner {
    background: linear-gradient(180deg, var(--sky-top) 0%, var(--sky-bottom) 100%);
  }
  .photo-couple-beach {
    position: absolute;
    left: 648px;
    top: 46px;
    width: 432px;
    height: 406px;
    background:
      radial-gradient(ellipse 45% 55% at 55% 60%, var(--skin-light) 0%, var(--skin-mid) 55%, rgba(201,149,120,0) 100%);
  }
  .photo-couple-bed {
    position: absolute;
    inset: 0;
    background:
      radial-gradient(ellipse 55% 60% at 70% 45%, var(--mono-mid) 0%, rgba(111,111,111,0) 70%),
      linear-gradient(160deg, var(--mono-light) 0%, var(--mono-mid) 45%, var(--mono-dark) 100%);
  }
  .offer-title {
    position: absolute;
    left: 38px;
    top: 40px;
    font-weight: 300;
    font-size: 59px;
    line-height: 1.2;
    color: var(--text-light);
    letter-spacing: -0.5px;
    white-space: nowrap;
    z-index: 2;
  }
  .offer-title strong {
    font-weight: 700;
    color: var(--accent);
  }
  .offer-price {
    position: absolute;
    left: 42px;
    top: 128px;
    font-weight: 400;
    font-size: 27px;
    color: var(--text-light);
    white-space: nowrap;
    z-index: 2;
  }
  .banner--mono .offer-title { top: 54px; }
  .banner--mono .offer-price { top: 142px; }
  .feature-band {
    position: absolute;
    left: 30px;
    top: 246px;
    width: 844px;
    height: 118px;
    background: var(--band);
    z-index: 1;
  }
  .feature-list {
    position: absolute;
    left: 46px;
    top: 254px;
    width: 880px;
    display: grid;
    grid-template-columns: 444px 436px;
    row-gap: 7px;
    list-style: none;
    z-index: 2;
  }
  .banner--mono .feature-list { top: 270px; }
  .feature-list li {
    display: flex;
    align-items: center;
    gap: 10px;
    font-size: 23px;
    line-height: 28px;
    color: var(--text-light);
    letter-spacing: -0.3px;
    white-space: nowrap;
  }
  .tick-box { width: 28px; height: 28px; flex: none; }
</style>
</head>
<body>
  <svg width="0" height="0" style="position:absolute">
    <defs>
      <symbol id="tick" viewBox="0 0 28 28">
        <rect x="2" y="3" width="23" height="23" rx="3" fill="none" stroke="#f7931e" stroke-width="2.5"/>
        <path d="M7 14 L12 20 L25 3" fill="none" stroke="#f7931e" stroke-width="3.5" stroke-linecap="round" stroke-linejoin="round"/>
      </symbol>
    </defs>
  </svg>

  <section class="banner banner--sky">
    <div class="banner__inner">
      <div class="photo-couple-beach" role="img" aria-label="Photo of a smiling couple embracing against a clear blue sky"></div>
      <h2 class="offer-title">10th <strong>Anniversary</strong> Offer</h2>
      <p class="offer-price">R 78,95 for 10 weeks</p>
      <div class="feature-band"></div>
      <ul class="feature-list">
        <li><svg class="tick-box"><use href="#tick"/></svg>Full Chatroom access &amp; 7 HD Cams</li>
        <li><svg class="tick-box"><use href="#tick"/></svg>View HD Adult Videos &amp; Photos</li>
        <li><svg class="tick-box"><use href="#tick"/></svg>Who’s looking at your Profile</li>
        <li><svg class="tick-box"><use href="#tick"/></svg>Advanced Member Search Filters</li>
        <li><svg class="tick-box"><use href="#tick"/></svg>Exclusive ‘Plus +’ Badge</li>
        <li><svg class="tick-box"><use href="#tick"/></svg>Totally unlimited messaging</li>
      </ul>
    </div>
  </section>

  <section class="banner banner--mono">
    <div class="banner__inner">
      <div class="photo-couple-bed" role="img" aria-label="Black and white photo of a couple embracing on a bed"></div>
      <h2 class="offer-title">10th <strong>Anniversary</strong> Offer</h2>
      <p class="offer-price">R 78,95 for 10 weeks</p>
      <ul class="feature-list">
        <li><svg class="tick-box"><use href="#tick"/></svg>Full Chatroom access &amp; 7 HD Cams</li>
        <li><svg class="tick-box"><use href="#tick"/></svg>View HD Adult Videos &amp; Photos</li>
        <li><svg class="tick-box"><use href="#tick"/></svg>Who’s looking at your Profile</li>
        <li><svg class="tick-box"><use href="#tick"/></svg>Advanced Member Search Filters</li>
        <li><svg class="tick-box"><use href="#tick"/></svg>Exclusive ‘Plus +’ Badge</li>
        <li><svg class="tick-box"><use href="#tick"/></svg>Totally unlimited messaging</li>
      </ul>
    </div>
  </section>
</body>
</html>
```